New business card for a regional office of a US M&A company

We need business card for a finance company, office based in Hong Kong , our Head office is in US, our business is to Merge and acquires companies , the new office will be a regional office for the Asia Pacific region. We want to use the head office logo as attached ( but don't have to be exactly the same, can be a variation to it) as a base and then add Asia Pacific alongside the logo.
We would prefer to have be bilingual Eng + Chinese, although we don't really have Chinese company name .

Industry/Entity Type

Business

Contact Information for Business Card

Clara Jo Tsang
 

VP,
APAC M&A Operations
ORIN VANTAGE Asia Pacific Limited
 
Unit 1407, K18
18 Tai Lok Shan Road, 
Hong Kong 
 
M: +852 6038 1742
T : +852 2836 4100
F : +852 2836 4177
VOIP: 4158
 
cjtsang@orinvantage.com

Font styles to use
Serif
Sans Serif

Colors

Designer to choose colors to be used in the design.

Requirements
Must have
• APAC Office

```html
<!DOCTYPE html>
<html lang="en">
<head>
<meta charset="utf-8">
<title>Orin Vantage Asia Pacific – Business Card</title>
<link rel="stylesheet" href="https://fonts.googleapis.com/css2?family=Ubuntu:wght@400;500;700&display=swap">
<style>
  :root {
    --backdrop: #e9eaec;
    --card-navy: #0e2742;
    --accent-cyan: #1fa3c9;
    --text-light: #e8eef4;
    --mark-white: #f2f4f6;
  }
  * { margin: 0; padding: 0; box-sizing: border-box; }
  html, body {
    width: 1200px; height: 576px; overflow: hidden;
    background: var(--backdrop);
    font-family: "Ubuntu", sans-serif;
  }
  .canvas { position: relative; width: 1200px; height: 576px; }
  .card {
    position: absolute; top: 139px;
    width: 484px; height: 293px;
    background: var(--card-navy);
    border-radius: 11px;
    overflow: hidden;
    border-bottom: 6px solid var(--accent-cyan);
  }
  .card--front { left: 82px; }
  .card--back { left: 602px; }

  .brand-square {
    position: absolute; left: 227px; top: 90px;
    width: 30px; height: 30px;
    background: var(--mark-white);
  }
  .brand-name {
    position: absolute; left: 0; right: 0; top: 160px;
    text-align: center;
    font-weight: 700; font-size: 38px; letter-spacing: 1px;
    color: var(--accent-cyan);
  }

  .holder-name {
    position: absolute; left: 17px; top: 25px;
    font-weight: 500; font-size: 18px; color: var(--accent-cyan);
  }
  .holder-title {
    position: absolute; left: 17px; top: 50px;
    font-size: 12px; line-height: 16px; color: var(--text-light);
  }
  .office-name {
    position: absolute; left: 17px; top: 160px;
    font-weight: 500; font-size: 15px; color: var(--accent-cyan);
  }
  .contact-list {
    position: absolute; left: 17px; top: 187px;
    list-style: none;
    font-size: 12px; line-height: 14.7px; color: var(--text-light);
  }
  .contact-list li { display: flex; align-items: center; }
  .contact-icon { width: 9px; height: 9px; margin-right: 11px; fill: var(--accent-cyan); flex: none; }
  .contact-label { color: var(--accent-cyan); margin-left: 6px; margin-right: 3px; }
  .office-address {
    position: absolute; left: 17px; top: 251px;
    font-size: 12px; color: var(--text-light);
  }
</style>
</head>
<body>
<main class="canvas">
  <section class="card card--front" aria-label="Card front">
    <div class="brand-square"></div>
    <div class="brand-name">ORIN VANTAGE</div>
  </section>

  <section class="card card--back" aria-label="Card back">
    <h1 class="holder-name">Clara Jo Tsang</h1>
    <p class="holder-title">Vice President,<br>APAC M&amp;A Operations</p>
    <h2 class="office-name">Orin Vantage Asia Pacific Limited</h2>
    <ul class="contact-list">
      <li>
        <svg class="contact-icon" viewBox="0 0 10 10"><rect x="2.5" y="0" width="5" height="10" rx="1"/></svg>
        +852 6038 1742
      </li>
      <li>
        <svg class="contact-icon" viewBox="0 0 10 10"><path d="M0 3 Q5 0 10 3 L10 4.5 L7.5 4.5 L7.5 3.5 L2.5 3.5 L2.5 4.5 L0 4.5Z M1.5 5.5 H8.5 V10 H1.5Z"/></svg>
        +852 2836 4100
      </li>
      <li>
        <svg class="contact-icon" viewBox="0 0 10 10"><rect x="2.5" y="0" width="5" height="3"/><rect x="0" y="3.5" width="10" height="4"/><rect x="2.5" y="8" width="5" height="2"/></svg>
        +852 2836 4177,<span class="contact-label">VOIP:</span>4158
      </li>
      <li>
        <svg class="contact-icon" viewBox="0 0 10 10"><path d="M0 2 H10 V8 H0Z" /><path d="M0 2 L5 5.5 L10 2" stroke="#0e2742" stroke-width="1" fill="none"/></svg>
        cjtsang@orinvantage.com
      </li>
    </ul>
    <p class="office-address">Unit 1407, K18, 18 Tai Lok Shan Road, Hong Kong</p>
  </section>
</main>
</body>
</html>
```